Velvet Lantern rebranding my business with a new business card

I have my new logo and now I need a refresher on my business cards. I really want something fun and fresh. I like black background or anything to make the color pop.
Logo
Name: Velvet Lantern
Contact Info as stated below:
Mira Pellow
555-013-4762
Logo
Name: Velvet Lantern
Mira Pellow
555-013-4762
fb.me/VelvetLanternbyMira
Instagram: @VelvetLanternbyMira

Industry/Entity Type

Business

Contact Information for Business Card

double-sided. Logo on one side. Contact info on the other.

Requirements
Must have
• Logo
• Name: Velvet Lantern
• Contact Info as stated below:
• Mira Pellow
• 555-013-4762
• fb.me/VelvetLanternbyMira
• fb.me/VelvetLanternbyMira

```html
<!DOCTYPE html>
<html lang="en">
<head>
<meta charset="utf-8">
<title>Velvet Lantern – Business Card</title>
<link href="https://fonts.googleapis.com/css2?family=Roboto:wght@400;500&family=Roboto+Condensed:wght@700&display=swap" rel="stylesheet">
<style>
  :root {
    --backdrop: #e8e4df;
    --card-pink: #f0a6b5;
    --card-white: #f4f4f4;
    --ink: #2b2b2b;
    --ink-soft: #555555;
    --url-grey: #6e5c61;
    --band-black: #0d0d0d;
    --accent-pink: #eda3b2;
    --logo-ink: #5a3a44;
  }
  * { box-sizing: border-box; margin: 0; padding: 0; }
  html, body { width: 1200px; height: 960px; overflow: hidden; }
  body {
    background: var(--backdrop);
    position: relative;
    font-family: "Roboto", Arial, sans-serif;
  }
  .card {
    position: absolute;
    left: 320px;
    width: 600px;
    height: 344px;
    border-radius: 18px;
    overflow: hidden;
    box-shadow: 0 6px 14px rgba(0,0,0,0.25);
  }
  .card-front { top: 106px; background: var(--card-pink); }
  .card-back  { top: 492px; background: var(--card-white); }

  .front-logo {
    position: absolute;
    left: 0; right: 0; top: 150px;
    text-align: center;
    font-family: "Roboto Condensed", Arial, sans-serif;
    font-weight: 700;
    font-size: 34px;
    color: var(--logo-ink);
  }
  .front-url {
    position: absolute;
    left: 0; right: 0; top: 292px;
    text-align: center;
    font-size: 14px;
    letter-spacing: 6px;
    color: var(--url-grey);
  }

  .logo-badge {
    position: absolute;
    left: 380px; top: 36px;
    width: 174px; height: 174px;
    border-radius: 50%;
    background: #ffffff;
    border: 2px solid var(--ink);
    box-shadow: inset 0 0 0 5px #ffffff, inset 0 0 0 7px var(--accent-pink);
    display: flex; align-items: center; justify-content: center;
    text-align: center;
    font-family: "Roboto Condensed", Arial, sans-serif;
    font-weight: 700;
    font-size: 22px;
    line-height: 1.1;
    color: var(--logo-ink);
  }
  .contact-name {
    position: absolute;
    left: 32px; top: 194px;
    font-family: "Roboto Condensed", Arial, sans-serif;
    font-weight: 700;
    font-size: 22px;
    color: var(--ink);
  }
  .contact-list {
    position: absolute;
    left: 33px; top: 236px;
    list-style: none;
    font-size: 14px;
    color: var(--ink-soft);
  }
  .contact-list li { display: flex; align-items: center; gap: 8px; height: 20px; }
  .contact-list svg { width: 13px; height: 13px; fill: var(--ink); }
  .icon-square { width: 11px; height: 11px; background: var(--ink); border-radius: 1px; margin-right: 2px; }

  .footer-band { position: absolute; left: 0; bottom: 0; width: 600px; height: 40px; }
  .footer-url {
    position: absolute;
    right: 18px; bottom: 12px;
    font-size: 14px;
    color: #ffffff;
  }
</style>
</head>
<body>

  <section class="card card-front" aria-label="Card front">
    <div class="front-logo">Velvet Lantern</div>
    <div class="front-url">www.velvetlantern.com</div>
  </section>

  <section class="card card-back" aria-label="Card back">
    <div class="logo-badge">Velvet<br>Lantern</div>

    <h1 class="contact-name">MIRA PELLOW</h1>
    <ul class="contact-list">
      <li>
        <svg viewBox="0 0 24 24" aria-hidden="true"><path d="M6.6 10.8a15.1 15.1 0 0 0 6.6 6.6l2.2-2.2a1 1 0 0 1 1-.25 11.4 11.4 0 0 0 3.6.57 1 1 0 0 1 1 1V20a1 1 0 0 1-1 1A17 17 0 0 1 3 4a1 1 0 0 1 1-1h3.5a1 1 0 0 1 1 1c0 1.25.2 2.45.57 3.57a1 1 0 0 1-.25 1z"/></svg>
        555-013-4762
      </li>
      <li><span class="icon-square" aria-hidden="true"></span>fb.me/VelvetLanternbyMira</li>
    </ul>

    <svg class="footer-band" viewBox="0 0 600 40" aria-hidden="true">
      <rect x="0" y="12" width="400" height="8" fill="var(--accent-pink)"/>
      <path d="M0 22 H400 Q408 22 412 14 Q416 4 428 4 H600 V40 H0 Z" fill="#ffffff"/>
      <path d="M0 24 H402 Q410 24 414 16 Q418 6 430 6 H600 V40 H0 Z" fill="var(--band-black)"/>
    </svg>
    <div class="footer-url">www.velvetlantern.com</div>
  </section>

</body>
</html>
```